Innovative Event Ticketing Start Up. Needs a Web Design

We need a web design for a new company based in London called 'Bandwise'. We are a platform which facilitates the building of groups of customers for events. As more people commit to an event, the price incrementally decreases. We would like there to be an emphasis on the sharing element and the decreasing price with higher participation.

Any quieres please email me at rvkm47@postlane.net

Target Market(s)

18-30 year olds who are active and savvy across social media sites

Industry/Entity Type

Events

Number of Pages Required

3 page

Font styles to use
Other font styles liked:
• Phi Roman

Requirements
Must have
• Each event offering runs for a limited time so a countdown timer is also to be included as well as a counter of number of participants (please find example attached).
• The interface needs to have the options for 'Live 'Music', 'Nightlife', 'Festivals', 'Comedy' and 'Everything Else'. Also
• A 'featured' section, for our promoted events
• Social sharing icons for Chatterbox, Flitter, PingTalk, SMS and Email
• Room the inclusion of a video
• Pages for clients to sign up - registering details ect.
• Content is still being completed, so room available to add when ready
Nice to have
• An interface design we like as a guiding templates on is https://quorvaapp.com/
• Luma wordpress theme is also of interest.
• Scroll over clicking for main interface and also for the event once clicked upon.
• Event pages similar desgin to quorva with same features such as Google Maps but also participant counter and affiliate marketing options.
Should not have
• CMS no longer necessary

```html
<!DOCTYPE html>
<html lang="en">
<head>
<meta charset="utf-8">
<title>Bandwise – Group Event Tickets</title>
<link href="https://fonts.googleapis.com/css2?family=Raleway:wght@400;500;600;700&display=swap" rel="stylesheet">
<style>
:root{
  --orange:#ef5b25;
  --orange-dark:#d94a17;
  --ink:#333;
  --muted:#9a9a9a;
  --line:#e4e4e4;
  --band:#f1f1f1;
  --white:#fff;
}
*{box-sizing:border-box;margin:0;padding:0}
html,body{width:1200px;height:3396px;overflow:hidden}
body{font-family:'Raleway',sans-serif;color:var(--ink);background:var(--white);position:relative}
.topbar{height:40px;display:flex;align-items:center;justify-content:space-between;padding:0 88px;border-bottom:1px solid var(--line);font-size:12px;color:var(--muted)}
.topbar .dots{display:flex;gap:14px}
.dot{width:12px;height:12px;border-radius:50%;background:#c9c9c9}
.login{display:flex;align-items:center;gap:6px}
.header{height:128px;display:flex;align-items:center;justify-content:space-between;padding:0 88px}
.brand{display:flex;align-items:center;gap:12px;font-size:40px;font-weight:600;color:var(--orange)}
.brand .mark{width:60px;height:60px;background:var(--orange);border-radius:8px}
.nav{display:flex;gap:34px;font-size:14px;font-weight:500}
.nav a{color:var(--ink);text-decoration:none}
.nav a.active{color:var(--orange)}
.hero{position:relative;height:492px;background:linear-gradient(110deg,#b97a5c 0%,#8b4b36 35%,#5a3128 65%,#c48f7a 100%)}
.hero-caption{position:absolute;left:88px;top:172px;width:472px;height:160px;background:rgba(255,255,255,.9);padding:26px 30px}
.hero-caption h2{font-size:30px;font-weight:600;color:var(--orange);margin-bottom:14px}
.hero-caption p{font-size:12px;line-height:1.6;color:#777}
.register{position:absolute;right:80px;top:24px;width:380px;height:440px;background:var(--white);box-shadow:0 4px 14px rgba(0,0,0,.25)}
.register h3{background:var(--orange);color:var(--white);text-align:center;font-size:28px;font-weight:500;padding:12px 0}
.register form{padding:18px 26px}
.register .field{height:36px;border:1px solid var(--line);margin-bottom:14px;font-size:12px;color:#aaa;display:flex;align-items:center;padding-left:12px}
.register .submit{margin:8px 0 0 auto;width:130px;height:44px;background:var(--orange);color:var(--white);display:flex;align-items:center;justify-content:center;font-size:16px}
.stats{height:320px;display:flex;justify-content:center;gap:76px;padding-top:52px}
.stat{width:180px;text-align:center}
.stat .circle{width:128px;height:128px;margin:0 auto 18px;border-radius:50%;background:var(--orange);border:6px solid #fbd3c3;color:var(--white);font-size:56px;font-weight:500;display:flex;align-items:center;justify-content:center}
.stat h4{color:var(--orange);font-size:15px;font-weight:600;margin-bottom:10px}
.stat p{font-size:11px;line-height:1.6;color:var(--muted)}
.events{height:1180px;background:var(--band);padding-top:44px;text-align:center}
.events .dots{display:flex;justify-content:center;gap:28px;margin-bottom:42px}
.events h2,.section-title{font-size:32px;font-weight:600;color:var(--orange)}
.intro{width:820px;margin:16px auto 0;font-size:12px;line-height:1.7;color:var(--muted)}
.grid{display:grid;grid-template-columns:repeat(4,240px);gap:52px 18px;justify-content:center;margin-top:58px;text-align:left}
.card{height:340px;background:var(--white)}
.card .photo{position:relative;height:160px}
.card .tag{position:absolute;left:10px;top:8px;background:var(--orange);color:var(--white);font-size:11px;padding:3px 10px}
.card .body{padding:14px}
.card .title{display:flex;justify-content:space-between;color:var(--orange);font-weight:600;font-size:15px;margin-bottom:12px}
.card .meta{display:flex;align-items:center;gap:8px;font-size:11px;color:var(--muted);margin-bottom:12px}
.card .ticket{display:inline-block;margin-top:6px;background:var(--orange);color:var(--white);font-size:13px;padding:10px 22px}
.more{display:inline-block;margin-top:48px;background:var(--orange);color:var(--white);font-size:15px;padding:16px 54px}
.about{height:380px;display:flex;justify-content:space-between;padding:32px 88px 0}
.about .text{width:600px}
.about p{margin-top:24px;font-size:12px;line-height:1.9;color:var(--muted)}
.video{width:344px;height:200px;margin-top:40px;position:relative;background:linear-gradient(135deg,#d9d4cf,#8e8178)}
.video .play{position:absolute;left:50%;top:50%;transform:translate(-50%,-50%)}
.collections{height:428px;text-align:center;padding-top:12px}
.coll-row{display:flex;justify-content:center;gap:16px;margin-top:46px;text-align:left}
.coll{width:500px;height:272px;display:flex;background:var(--white);box-shadow:0 2px 8px rgba(0,0,0,.12)}
.coll .photo{width:250px}
.coll .info{padding:18px}
.coll h4{color:var(--orange);font-size:16px;font-weight:600;margin-bottom:12px}
.coll p{font-size:12px;line-height:1.8;color:var(--muted)}
.footer{height:280px;background:var(--orange);color:var(--white);display:flex;padding:40px 88px 0}
.footer h5{font-size:15px;font-weight:600;margin-bottom:18px}
.footer ul{list-style:none;font-size:11px;line-height:2.1}
.footer li{display:flex;align-items:center;gap:8px}
.footer .ic{width:9px;height:9px;border-radius:50%;background:rgba(255,255,255,.8)}
.map{width:220px;height:116px;background:#e5e1dc;margin:38px 0 0 40px}
.f-contact{width:232px}
.f-links{margin-left:220px;width:200px}
.f-social{margin-left:40px}
.bottom{height:116px;background:var(--orange-dark);color:var(--white);font-size:12px;display:flex;align-items:center;justify-content:center;border-top:1px solid rgba(255,255,255,.3)}
</style>
</head>
<body>
<div class="topbar">
  <div class="dots"><span class="dot"></span><span class="dot"></span><span class="dot"></span><span class="dot"></span></div>
  <div class="login"><svg width="10" height="10" viewBox="0 0 10 10"><circle cx="5" cy="3" r="2.5" fill="#bbb"/><rect x="1" y="6" width="8" height="4" rx="2" fill="#bbb"/></svg>Login / Register</div>
</div>
<header class="header">
  <div class="brand"><span class="mark"></span>Bandwise</div>
  <nav class="nav"><a class="active" href="#">Home</a><a href="#">About us</a><a href="#">Latest Events</a><a href="#">Live Events</a><a href="#">Blog</a><a href="#">Contact Us</a></nav>
</header>
<section class="hero" role="img" aria-label="Guitarist performing on stage under warm lights">
  <div class="hero-caption">
    <h2>Live Music</h2>
    <p>Join friends, fill the room and watch the ticket price drop as more fans commit to the same night out together.</p>
  </div>
  <div class="register">
    <h3>Register Form</h3>
    <form>
      <div class="field">Name</div><div class="field">E-Mail</div><div class="field">Phone</div>
      <div class="field">Last Name</div><div class="field">Password</div><div class="field">Re-Enter Password</div>
      <div class="submit">Submit</div>
    </form>
  </div>
</section>
<section class="stats">
  <div class="stat"><div class="circle">99</div><h4>Live Music</h4><p>Gigs and concerts across town, cheaper every time another friend signs up.</p></div>
  <div class="stat"><div class="circle">125</div><h4>Live Nightlife</h4><p>Club nights and bars where bigger groups unlock better prices for all.</p></div>
  <div class="stat"><div class="circle">53</div><h4>Live Festivals</h4><p>Weekend festivals with group passes that fall as the crowd grows.</p></div>
  <div class="stat"><div class="circle">104</div><h4>Live Comedy</h4><p>Stand-up shows and open mics, shared laughs at a shared lower price.</p></div>
</section>
<section class="events">
  <div class="dots"><span class="dot"></span><span class="dot"></span><span class="dot"></span><span class="dot"></span><span class="dot"></span></div>
  <h2>Welcome to Bandwise</h2>
  <p class="intro">Bandwise brings people together for the events they love. Every event runs for a limited time, and as more people commit, the ticket price steps down for everyone in the group. Share it and save.</p>
  <div class="grid">
    <div class="card"><div class="photo" role="img" aria-label="Guitar player on stage" style="background:linear-gradient(135deg,#5b4a3d,#1d1712)"><span class="tag">Music</span></div><div class="body"><div class="title">Live Music<span>‹</span></div><div class="meta">▣ Jan 15th / 2016</div><div class="meta">⌖ City, Place / Landmark</div><span class="ticket">Get Tickets</span></div></div>
    <div class="card"><div class="photo" role="img" aria-label="Microphone under stage lights" style="background:linear-gradient(135deg,#8a6a4a,#2a2a3a)"><span class="tag">Comedy</span></div><div class="body"><div class="title">Live Comedy<span>‹</span></div><div class="meta">▣ Jan 15th / 2016</div><div class="meta">⌖ City, Place / Landmark</div></div></div>
    <div class="card"><div class="photo" role="img" aria-label="Sky lanterns at a night festival" style="background:linear-gradient(135deg,#e9a33a,#3a1c0c)"><span class="tag">Festival</span></div><div class="body"><div class="title">Live Festival<span>‹</span></div><div class="meta">▣ Jan 15th / 2016</div><div class="meta">⌖ City, Place / Landmark</div></div></div>
    <div class="card"><div class="photo" role="img" aria-label="Dancers at a club night" style="background:linear-gradient(135deg,#6a3a7a,#1b1030)"><span class="tag">Nightlife</span></div><div class="body"><div class="title">Live Night Party<span>‹</span></div><div class="meta">▣ Jan 15th / 2016</div><div class="meta">⌖ City, Place / Landmark</div></div></div>
    <div class="card"><div class="photo" role="img" aria-label="Colourful street festival" style="background:linear-gradient(135deg,#6f8fb8,#b44a3a)"><span class="tag">Festival</span></div><div class="body"><div class="title">Live Festival<span>‹</span></div><div class="meta">▣ Jan 15th / 2016</div><div class="meta">⌖ City, Place / Landmark</div></div></div>
    <div class="card"><div class="photo" role="img" aria-label="Hands playing an acoustic guitar" style="background:linear-gradient(135deg,#c9bfb3,#6e655c)"><span class="tag">Music</span></div><div class="body"><div class="title">Live Music<span>‹</span></div><div class="meta">▣ Jan 15th / 2016</div><div class="meta">⌖ City, Place / Landmark</div></div></div>
    <div class="card"><div class="photo" role="img" aria-label="Friends celebrating at a party" style="background:linear-gradient(135deg,#d9a0b8,#7a3a5a)"><span class="tag">Nightlife</span></div><div class="body"><div class="title">Live Night Party<span>‹</span></div><div class="meta">▣ Jan 15th / 2016</div><div class="meta">⌖ City, Place / Landmark</div></div></div>
    <div class="card"><div class="photo" role="img" aria-label="Theatre comedy and tragedy masks" style="background:linear-gradient(135deg,#e0b040,#8a1e12)"><span class="tag">Comedy</span></div><div class="body"><div class="title">Live Comedy<span>‹</span></div><div class="meta">▣ Jan 15th / 2016</div><div class="meta">⌖ City, Place / Landmark</div></div></div>
  </div>
  <span class="more">Show More</span>
</section>
<section class="about">
  <div class="text">
    <h2 class="section-title">What we do ?</h2>
    <p>We help groups form around events. Pick a gig, a club night, a festival or a comedy show, then share it with your friends. Each new person who commits lowers the price a little more, and a live counter shows how many have joined while the countdown shows how long is left. When the timer ends, everyone pays the final, lowest price. It is simple, social and built for people who love going out together and hate paying full price on their own.</p>
  </div>
  <div class="video" role="img" aria-label="Video preview of a concert crowd">
    <svg class="play" width="64" height="64" viewBox="0 0 64 64"><circle cx="32" cy="32" r="30" fill="rgba(255,255,255,.8)"/><path d="M26 20 L46 32 L26 44Z" fill="#ef5b25"/></svg>
  </div>
</section>
<section class="collections">
  <h2 class="section-title">Our Collections</h2>
  <div class="coll-row">
    <div class="coll"><div class="photo" role="img" aria-label="Electric guitar being played" style="background:linear-gradient(135deg,#7a5a3a,#1a120c)"></div><div class="info"><h4>Music</h4><p>Concerts and gigs from small rooms to big arenas, all priced by the crowd that joins.</p></div></div>
    <div class="coll"><div class="photo" role="img" aria-label="Crowd with raised hands at a concert" style="background:linear-gradient(135deg,#3a3a3a,#0e0e0e)"></div><div class="info"><h4>Partys</h4><p>Club nights and parties where every new guest makes the night cheaper for the whole group.</p></div></div>
  </div>
</section>
<footer class="footer">
  <div class="f-contact"><h5>Contact Us</h5><ul><li><span class="ic"></span>Address Line 1, Address Line 2</li><li><span class="ic"></span>City, Place, Country</li><li><span class="ic"></span>hello@bandwise.net</li><li><span class="ic"></span>020 555 0142</li></ul></div>
  <div class="map" role="img" aria-label="Location map"></div>
  <div class="f-links"><h5>Quick Link</h5><ul><li>Home</li><li>About us</li><li>Latest Events</li><li>Live Events</li><li>Blog</li><li>Contact Us</li></ul></div>
  <div class="f-social"><h5>Social Media</h5><ul><li><span class="ic"></span>Chatterbox</li><li><span class="ic"></span>Flitter</li><li><span class="ic"></span>Linkup</li><li><span class="ic"></span>Circlecast</li></ul></div>
</footer>
<div class="bottom">© 2015 · Bandwise · All Rights Reserved</div>
</body>
</html>
```